Tide & Thistle Website Creation For Online Spirits Sales via MerrowVats.com

Want a Website developed that I will use to partner with Merrow Vats to sell my signature rum online. Merrow Vats will add the final code to make the website an e-commerce site. Website should have links to Social media pages, recipies, About, news and events, products. I have he domain name already just need a designer to make the website look professional. Need website capable of being viewed on iPhone and Android devices. Please use the color scheme that is on the label. The brand motto is: Celebrate Life With Family old and new friends. The bottle sent in the images will be replaced with and actual high resolution image of the bottle when it is produce on 27 DEC 21. Can give the selected designer access to develop the website. I have the hostbramble.com domain name. Final code will be added by a designer from MerrowVats.com to make it a e-commerce store.
Updates

I added more information to refine the design I wanted. I should have had this information available to the designers when I started the project.

Target Market(s)

Target Market is 25-50 year old who drink rum

Industry/Entity Type

Spirits. Using Website to sell Rum online

Number of Pages Required

1 page

Font styles to use
Sans Serif

Colors
00AB8E
00BBA5
67D7C9
C6EFE9
E9F9F6

Requirements
Must have
• Must look elegant and of high class. Rum is being market as a premium unnamed rum.
Nice to have
• Video of people drinking, smiling and celebrating

```html
<!DOCTYPE html>
<html lang="en">
<head>
<meta charset="utf-8">
<title>Tide &amp; Thistle</title>
<link href="https://fonts.googleapis.com/css2?family=Roboto:ital,wght@0,400;0,500;0,700;1,400&family=Libre+Baskerville:wght@700&display=swap" rel="stylesheet">
<style>
:root{
  --green:#00AB8E;
  --green-2:#00BBA5;
  --green-3:#67D7C9;
  --mint:#C6EFE9;
  --mint-soft:#E9F9F6;
  --ink:#111;
  --text:#555;
  --muted:#888;
  --line:#e2e2e2;
  --gold:#f5b301;
  --footer:#2b2b2b;
}
*{margin:0;padding:0;box-sizing:border-box}
html,body{width:1200px;height:4135px;overflow:hidden}
body{font-family:'Roboto',sans-serif;color:var(--text);background:#fff;position:relative}
.abs{position:absolute}
.serif{font-family:'Libre Baskerville',serif;font-weight:700;color:var(--ink);text-transform:uppercase}
.section-title{position:absolute;left:0;width:1200px;text-align:center;font-size:32px;letter-spacing:.5px}

/* header */
.header{position:absolute;top:0;left:0;width:1200px;height:115px;background:#fff}
.brand{position:absolute;left:105px;top:18px;width:205px;text-align:center}
.brand-dot{width:52px;height:52px;border-radius:50%;background:var(--ink);margin:0 auto 6px}
.brand-name{font-family:'Libre Baskerville',serif;font-weight:700;font-size:22px;color:var(--ink);white-space:nowrap}
.welcome{left:347px;top:20px;font-size:13px;font-weight:700;color:var(--green)}
.topbar{top:20px;font-size:13px;font-weight:700;color:#333}
.flag{left:744px;top:19px;width:24px;height:14px;background:linear-gradient(#b22 0 50%,#fff 50% 60%,#b22 60%);}
.flag::before{content:"";position:absolute;left:0;top:0;width:10px;height:8px;background:#2a3e8c}
.sep{top:17px;width:1px;height:20px;background:var(--line)}
.nav{position:absolute;left:347px;top:78px;display:flex;gap:33px;font-size:13.5px;font-weight:700;color:var(--ink)}
.nav .on{color:var(--green);border-bottom:2px solid var(--green);padding-bottom:5px}

/* hero */
.hero{position:absolute;top:115px;left:0;width:1200px;height:599px;background:radial-gradient(ellipse at 45% 45%,#7a5230 0%,#3b2416 45%,#140c08 100%)}
.hero-title{position:absolute;top:410px;width:1200px;text-align:center;color:#fff;font-size:34px;line-height:43px}
.dots{position:absolute;left:1140px;top:236px;display:flex;flex-direction:column;gap:10px}
.dots span{width:9px;height:9px;border-radius:50%;background:#fff}
.dots .ring{background:none;border:2px solid #fff}

/* products */
.card{position:absolute;top:873px;width:237px;height:332px;border:1px solid var(--line);background:#fff;text-align:center}
.card.lift{box-shadow:0 4px 14px rgba(0,0,0,.12)}
.bottle{width:58px;height:185px;margin:18px auto 0;border-radius:8px 8px 18px 18px;background:linear-gradient(#d6d6d6 0 14%,#c9862f 14%,#e0a34d 55%,#b06a20)}
.p-title{margin-top:26px;font-size:14px;font-weight:700;color:var(--ink)}
.price{margin-top:12px;font-size:25px;font-weight:500;color:var(--green)}
.stars{position:absolute;left:40px;bottom:30px;color:var(--gold);font-size:13px;letter-spacing:1px}
.cart{position:absolute;right:38px;bottom:22px;width:32px;height:30px;border:2px solid var(--green);display:flex;align-items:center;justify-content:center}
.cart.fill{background:var(--green)}
.btn{position:absolute;background:var(--green);color:#fff;font-size:13px;font-weight:700;display:flex;align-items:center;justify-content:center;gap:9px}
.btn i{width:14px;height:14px;border-radius:50%;background:#fff;display:inline-block;position:relative}
.btn i::after{content:"";position:absolute;left:4px;top:4px;border-left:6px solid var(--green);border-top:3px solid transparent;border-bottom:3px solid transparent}

/* about */
.about{position:absolute;top:1405px;left:0;width:1200px;height:565px;background:linear-gradient(100deg,var(--green) 0%,var(--green-2) 60%,#0a8f78 100%)}
.photo-back{position:absolute;left:111px;top:82px;width:409px;height:289px;background:linear-gradient(135deg,#e8e2d6,#a79884)}
.photo-front{position:absolute;left:200px;top:262px;width:365px;height:219px;background:linear-gradient(135deg,#3a1f2c,#7b4a3a);border:8px solid var(--green)}
.about h2{position:absolute;left:659px;top:132px;color:#fff;font-size:32px}
.about p{position:absolute;left:661px;top:183px;width:425px;color:#fff;font-size:14px;line-height:25.7px}
.about .btn{left:661px;top:388px;width:154px;height:48px;background:var(--green-2);border:1px solid var(--green-3)}

/* solutions */
.sol{position:absolute;top:2164px;width:318px;height:326px;border:1px solid var(--line);border-radius:12px;background:#fff;text-align:center}
.sol.lift{box-shadow:0 6px 20px rgba(0,0,0,.12);border-bottom:5px solid var(--green)}
.sol-icon{width:86px;height:86px;border-radius:50%;background:#c4c4c4;margin:20px auto 0;display:flex;align-items:center;justify-content:center}
.sol.lift .sol-icon{background:var(--green)}
.sol h3{margin-top:30px;font-size:15.5px;font-weight:700;color:var(--ink)}
.sol hr{width:38px;border:0;border-top:2px solid #ccc;margin:12px auto 14px}
.sol p{font-size:13px;line-height:21.5px;color:#666;width:270px;margin:0 auto}
.sol a{display:inline-block;margin-top:22px;font-size:12.5px;font-weight:500;color:#555;text-decoration:underline}
.sol.lift a{color:var(--green)}
.arrow{position:absolute;top:2316px;width:26px;height:22px;border:1px solid var(--line);display:flex;align-items:center;justify-content:center}

/* testimonials */
.clients{position:absolute;top:2598px;left:0;width:1200px;height:442px;background:linear-gradient(180deg,var(--green-2),var(--green) 60%,#078f76)}
.clients h2{position:absolute;top:68px;width:1200px;text-align:center;color:#fff;font-size:32px}
.quote{position:absolute;top:147px;width:321px;height:143px;background:#fff;padding:28px 20px 0}
.quote.dark{background:var(--green)}
.quote p{font-style:italic;font-size:13.5px;line-height:25.5px;color:#555}
.quote.dark p{color:#fff}
.quote::after{content:"";position:absolute;left:20px;bottom:-12px;border-top:12px solid #fff;border-right:12px solid transparent;border-left:12px solid transparent}
.quote.dark::after{border-top-color:var(--green)}
.qmark{position:absolute;right:20px;bottom:16px;font-family:'Libre Baskerville',serif;font-size:48px;line-height:30px;color:var(--green)}
.quote.dark .qmark{color:#fff}
.person{position:absolute;top:318px;display:flex;align-items:center;gap:20px;color:#fff}
.avatar{width:54px;height:54px;border-radius:50%;background:#cfd8d6;border:3px solid #fff}
.person b{display:block;font-size:13px}
.person span{font-size:13px}
.person .stars{position:static;color:var(--gold);font-size:14px;margin-left:26px}

/* news */
.news{position:absolute;top:3211px;width:318px}
.news-img{height:219px;background:linear-gradient(135deg,#5a3a22,#23160e)}
.news h4{margin:34px 0 0 13px;font-size:14px;font-weight:700;color:var(--ink)}
.news hr{width:38px;border:0;border-top:3px solid var(--green);margin:12px 0 14px 13px}
.news p{margin-left:13px;font-size:13.5px;line-height:24px;color:#666;width:290px}
.meta{margin:16px 10px 0;border-top:1px solid var(--line);padding:14px 0 0 14px;display:flex;gap:40px;font-size:12.5px;color:#666}
.meta span{display:flex;align-items:center;gap:12px}

/* footer */
.footer{position:absolute;top:3725px;left:0;width:1200px;height:357px;background:var(--footer);color:#ddd}
.f-logo{position:absolute;left:132px;top:86px;width:186px;height:186px;border-radius:50%;border:8px solid #fff;display:flex;align-items:center;justify-content:center}
.f-logo span{font-family:'Libre Baskerville',serif;font-weight:700;font-size:19px;color:#fff;text-align:center;line-height:28px}
.f-head{position:absolute;top:86px;font-size:13px;font-weight:700;color:#fff}
.f-head::after{content:"";display:block;width:40px;height:3px;background:var(--green);margin-top:14px}
.links{position:absolute;left:396px;top:140px;list-style:none;font-size:13px;line-height:30px}
.links li::before{content:"»";color:var(--green);margin-right:18px}
.contact{position:absolute;left:577px;top:140px;font-size:12.5px;color:#eee}
.contact div{display:flex;align-items:center;gap:18px;height:44px}
.contact i{width:24px;height:24px;border-radius:50%;background:#3b3b3b;display:flex;align-items:center;justify-content:center;flex:none}
.sub-text{position:absolute;left:823px;top:140px;width:260px;font-size:13px;line-height:21px}
.sub-form{position:absolute;left:823px;top:196px;width:257px;height:47px;border-radius:24px;background:#fff;display:flex;align-items:center;padding-left:26px;gap:14px;font-size:12.5px;color:#666}
.sub-form b{position:absolute;right:0;top:0;width:45px;height:47px;border-radius:0 24px 24px 0;background:var(--green);display:flex;align-items:center;justify-content:center}
.social{position:absolute;left:823px;top:263px;display:flex;gap:10px}
.social span{width:31px;height:31px;border-radius:50%;background:#fff;border:4px solid var(--green)}
.copy{position:absolute;top:4082px;left:0;width:1200px;height:53px;background:var(--green);color:#fff;font-size:13px;text-align:center;line-height:53px}
</style>
</head>
<body>

<header class="header">
  <div class="brand"><div class="brand-dot"></div><div class="brand-name">TIDE &amp; THISTLE</div></div>
  <div class="abs welcome">WELCOME TO TIDE &amp; THISTLE</div>
  <div class="abs flag"></div>
  <div class="abs topbar" style="left:793px">ENG ⌄</div>
  <div class="abs sep" style="left:869px"></div>
  <div class="abs topbar" style="left:894px">USD ⌄</div>
  <div class="abs sep" style="left:970px"></div>
  <div class="abs topbar" style="left:998px">(0) ITEMS
    <svg width="12" height="11" viewBox="0 0 12 11"><path d="M0 1h2l2 6h6l2-5H3" fill="none" stroke="#333" stroke-width="1.6"/><circle cx="5" cy="9.5" r="1.2" fill="#333"/><circle cx="9" cy="9.5" r="1.2" fill="#333"/></svg>
  </div>
  <nav class="nav">
    <span class="on">HOME</span><span>ABOUT US</span><span>OUR PRODUCTS</span><span>CATEGORIES</span><span>LATEST BLOG</span><span>REVIEWS</span><span>CONTACT US</span>
  </nav>
</header>

<section class="hero" role="img" aria-label="Friends raising glasses together at a warm, candlelit bar">
  <h1 class="hero-title serif" style="color:#fff">Celebrate life with family,<br>old &amp; new friends</h1>
  <div class="dots"><span></span><span></span><span class="ring"></span><span></span><span></span></div>
</section>

<h2 class="section-title serif" style="top:785px">Featured Products</h2>

<div class="card" style="left:111px"><div class="bottle" role="img" aria-label="Rum bottle"></div><div class="p-title">PRODUCT TITLE</div><div class="price">$ 23.00</div><div class="stars">★★★★★</div><div class="cart"><svg width="16" height="14" viewBox="0 0 12 11"><path d="M0 1h2l2 6h6l2-5H3" fill="none" stroke="#00AB8E" stroke-width="1.6"/><circle cx="5" cy="9.5" r="1.2" fill="#00AB8E"/><circle cx="9" cy="9.5" r="1.2" fill="#00AB8E"/></svg></div></div>
<div class="card" style="left:357px"><div class="bottle" role="img" aria-label="Rum bottle"></div><div class="p-title">PRODUCT TITLE</div><div class="price">$ 23.00</div><div class="stars">★★★★★</div><div class="cart"><svg width="16" height="14" viewBox="0 0 12 11"><path d="M0 1h2l2 6h6l2-5H3" fill="none" stroke="#00AB8E" stroke-width="1.6"/><circle cx="5" cy="9.5" r="1.2" fill="#00AB8E"/><circle cx="9" cy="9.5" r="1.2" fill="#00AB8E"/></svg></div></div>
<div class="card lift" style="left:604px"><div class="bottle" role="img" aria-label="Rum bottle"></div><div class="p-title">PRODUCT TITLE</div><div class="price">$ 23.00</div><div class="stars">★★★★★</div><div class="cart fill"><svg width="16" height="14" viewBox="0 0 12 11"><path d="M0 1h2l2 6h6l2-5H3" fill="none" stroke="#fff" stroke-width="1.6"/><circle cx="5" cy="9.5" r="1.2" fill="#fff"/><circle cx="9" cy="9.5" r="1.2" fill="#fff"/></svg></div></div>
<div class="card" style="left:851px"><div class="bottle" role="img" aria-label="Rum bottle"></div><div class="p-title">PRODUCT TITLE</div><div class="price">$ 23.00</div><div class="stars">★★★★★</div><div class="cart"><svg width="16" height="14" viewBox="0 0 12 11"><path d="M0 1h2l2 6h6l2-5H3" fill="none" stroke="#00AB8E" stroke-width="1.6"/><circle cx="5" cy="9.5" r="1.2" fill="#00AB8E"/><circle cx="9" cy="9.5" r="1.2" fill="#00AB8E"/></svg></div></div>

<div class="btn" style="left:499px;top:1261px;width:202px;height:48px;border-radius:24px">VIEW ALL PRODUCTS <i></i></div>

<section class="about">
  <div class="photo-back" role="img" aria-label="Friends cheering on a sofa at home"></div>
  <div class="photo-front" role="img" aria-label="Group toasting at a night party"></div>
  <h2 class="serif" style="color:#fff">About Us</h2>
  <p>Tide &amp; Thistle fulfillment services operate through a national network of licensed retailers, shipping carriers, and customer service professionals to guarantee the best fulfillment and logistics practices. Tide &amp; Thistle fulfillment services operate through a national network of licensed retailers, shipping carriers, and customer service professionals to guarantee the best fulfillment and logistics practices.</p>
  <div class="btn">LEARN MORE <i></i></div>
</section>

<h2 class="section-title serif" style="top:2075px">Our Solutions</h2>

<div class="arrow" style="left:26px"><svg width="20" height="8" viewBox="0 0 20 8"><path d="M20 4H2M5 1L1 4l4 3" fill="none" stroke="#111" stroke-width="1.6"/></svg></div>
<div class="arrow" style="left:1132px"><svg width="20" height="8" viewBox="0 0 20 8"><path d="M0 4h18M15 1l4 3-4 3" fill="none" stroke="#111" stroke-width="1.6"/></svg></div>

<div class="sol" style="left:99px">
  <div class="sol-icon"><svg width="38" height="38" viewBox="0 0 24 24"><path d="M3 12l9-9h8v8l-9 9z" fill="#111"/><circle cx="16" cy="8" r="1.8" fill="#c4c4c4"/></svg></div>
  <h3>WHITE-LABEL</h3><hr>
  <p>Back in 2014, Tide &amp; Thistle brought technology and customization into the beverage industry by being</p>
  <a>LEARN MORE ⊙</a>
</div>
<div class="sol lift" style="left:441px">
  <div class="sol-icon"><svg width="42" height="36" viewBox="0 0 26 22"><rect x="1" y="5" width="22" height="15" fill="none" stroke="#fff" stroke-width="2"/><path d="M1 5l11 8 11-8" fill="none" stroke="#fff" stroke-width="2"/><rect x="14" y="1" width="11" height="8" fill="#00AB8E" stroke="#fff" stroke-width="1.5"/></svg></div>
  <h3>SUBSCRIPTIONS</h3><hr>
  <p>Subscriptions models are among some of the most successful strategies within the e-commerce arena</p>
  <a>LEARN MORE ⊙</a>
</div>
<div class="sol" style="left:783px">
  <div class="sol-icon"><svg width="42" height="36" viewBox="0 0 26 22"><path d="M2 21h22" stroke="#111" stroke-width="2"/><rect x="4" y="13" width="3" height="7" fill="#111"/><rect x="9" y="9" width="3" height="11" fill="#111"/><rect x="14" y="11" width="3" height="9" fill="#111"/><rect x="19" y="5" width="3" height="15" fill="#111"/><path d="M3 10l6-5 5 3 7-6" fill="none" stroke="#111" stroke-width="1.5"/></svg></div>
  <h3>ANALYTICS SUITE</h3><hr>
  <p>CRM and interactive reporting platform provides analytics on traffic sourcing, conversion ratios</p>
  <a>LEARN MORE ⊙</a>
</div>

<section class="clients" role="img" aria-label="Teal tinted backdrop of palm trees">
  <h2 class="serif" style="color:#fff">What our clients say</h2>
  <div class="quote" style="left:111px"><p>Sed ut perspiciatis unde omnis iste natus error sit voluptatem accusantiudoloremque laudantium, totam rem aperiam</p><span class="qmark">”</span></div>
  <div class="quote dark" style="left:440px"><p>Sed ut perspiciatis unde omnis iste natus error sit voluptatem accusantiudoloremque laudantium, totam rem aperiam</p><span class="qmark">”</span></div>
  <div class="quote" style="left:768px"><p>Sed ut perspiciatis unde omnis iste natus error sit voluptatem accusantiudoloremque laudantium, totam rem aperiam</p><span class="qmark">”</span></div>
  <div class="person" style="left:130px"><div class="avatar"></div><div><b>NORA VALE</b><span>Businessman</span></div><span class="stars">★★★★★</span></div>
  <div class="person" style="left:459px"><div class="avatar"></div><div><b>NORA VALE</b><span>Businessman</span></div><span class="stars">★★★★★</span></div>
  <div class="person" style="left:787px"><div class="avatar"></div><div><b>NORA VALE</b><span>Businessman</span></div><span class="stars">★★★★★</span></div>
</section>

<h2 class="section-title serif" style="top:3127px">Latest News</h2>

<article class="news" style="left:111px">
  <div class="news-img" role="img" aria-label="Friends toasting with beer at a bar"></div>
  <h4>PERSPICIATIS UNDE</h4><hr>
  <p>Lorem ipsum dolor sit amet, consectetur adipiscing elit, sed do eiusmod tempor incididunt ut labore et dolor</p>
  <div class="meta"><span>▦ Sep 01 , 2021</span><span>◌ No Comments</span></div>
</article>
<article class="news" style="left:441px">
  <div class="news-img" role="img" aria-label="Crowd celebrating in a busy pub" style="background:linear-gradient(135deg,#4a3324,#1c130d)"></div>
  <h4>PERSPICIATIS UNDE</h4><hr>
  <p>Lorem ipsum dolor sit amet, consectetur adipiscing elit, sed do eiusmod tempor incididunt ut labore et dolor</p>
  <div class="meta"><span>▦ Sep 01 , 2021</span><span>◌ No Comments</span></div>
</article>
<article class="news" style="left:771px">
  <div class="news-img" role="img" aria-label="Holiday dinner toast with red wine" style="background:linear-gradient(135deg,#6b3e2a,#2b1a12)"></div>
  <h4>PERSPICIATIS UNDE</h4><hr>
  <p>Lorem ipsum dolor sit amet, consectetur adipiscing elit, sed do eiusmod tempor incididunt ut labore et dolor</p>
  <div class="meta"><span>▦ Sep 01 , 2021</span><span>◌ No Comments</span></div>
</article>

<footer class="footer">
  <div class="f-logo"><span>TIDE &amp;<br>THISTLE</span></div>
  <div class="f-head" style="left:396px">QUICK LINKS</div>
  <ul class="links"><li>Home</li><li>About Us</li><li>Our Products</li><li>Reviews</li><li>Contact Us</li></ul>
  <div class="f-head" style="left:577px">CONTACT US</div>
  <div class="contact">
    <div><i><svg width="11" height="11" viewBox="0 0 12 12"><path d="M2 1l3 0 1 3-2 1a7 7 0 003 3l1-2 3 1v3c-6 0-10-4-9-9z" fill="#fff"/></svg></i>1 800 555 0142</div>
    <div><i><svg width="11" height="9" viewBox="0 0 12 9"><rect x="0.5" y="0.5" width="11" height="8" fill="none" stroke="#fff"/><path d="M0.5 .5l5.5 4 5.5-4" fill="none" stroke="#fff"/></svg></i>hello@tideandthistle.co.nz</div>
    <div style="line-height:15px"><i><svg width="9" height="12" viewBox="0 0 9 12"><path d="M4.5 12S0 7 0 4.5a4.5 4.5 0 019 0C9 7 4.5 12 4.5 12z" fill="#fff"/><circle cx="4.5" cy="4.5" r="1.5" fill="#3b3b3b"/></svg></i>PO Box 3150 Harbourview<br>United States</div>
    <div><i><svg width="11" height="11" viewBox="0 0 12 12"><path d="M1 2l3-1 4 2 3-1v9l-3 1-4-2-3 1z" fill="#fff"/></svg></i><u>View Other Location</u></div>
  </div>
  <div class="f-head" style="left:823px">SUBSCRIBE NOW</div>
  <p class="sub-text">Sed ut perspiciatis unde omnis iste natus error sit voluptatem accusantium</p>
  <div class="sub-form"><svg width="12" height="9" viewBox="0 0 12 9"><rect width="12" height="9" fill="#555"/><path d="M0 0l6 5 6-5" fill="none" stroke="#fff"/></svg>Email Address<b><svg width="14" height="14" viewBox="0 0 14 14"><path d="M0 6l14-6-5 14-2-6z" fill="#fff"/></svg></b></div>
  <div class="social"><span></span><span></span><span></span><span></span></div>
</footer>
<div class="copy">© 2021 Tide &amp; Thistle . All Rights Reserved</div>

</body>
</html>
```